Realty Group Needs Classy, Contemporary Letterhead Design

We need a letterhead design for a new realty company located in NY, USA. We buy investment properties to rehabilitate and or keep in our rental portfolio.

```html
<!DOCTYPE html>
<html lang="en">
<head>
<meta charset="utf-8">
<title>Meridian Realty Group — Letterhead</title>
<link href="https://fonts.googleapis.com/css2?family=Montserrat:wght@400;500;700&display=swap" rel="stylesheet">
<style>
  :root {
    --purple: #4f2a8a;
    --ink: #2b2b2b;
    --rule-grey: #8a8a8a;
    --paper: #ffffff;
    --backdrop: #e6e6e6;
  }
  * { box-sizing: border-box; margin: 0; padding: 0; }
  html, body { width: 1200px; height: 803px; overflow: hidden; }
  body {
    background: var(--backdrop);
    font-family: "Montserrat", sans-serif;
    color: var(--ink);
  }
  .letterhead {
    position: absolute;
    left: 331px; top: 21px;
    width: 538px; height: 760px;
    background: var(--paper);
    overflow: hidden;
    box-shadow: 0 4px 18px rgba(0,0,0,.18);
  }
  .brand {
    position: absolute; left: 42px; top: 76px;
    font-weight: 700; font-size: 17px; line-height: 1.2;
    color: var(--purple);
  }
  .contact { position: absolute; left: 356px; top: 44px; list-style: none; }
  .contact li {
    display: flex; align-items: center; gap: 8px;
    font-size: 8.4px; line-height: 11px; color: var(--ink);
    margin-bottom: 5px;
  }
  .contact svg { width: 14px; height: 14px; flex: none; }
  .header-rule {
    position: absolute; left: 42px; top: 130px;
    width: 445px; height: 1.5px; background: var(--purple);
  }
  .letter-body {
    position: absolute; left: 42px; top: 184px; width: 445px;
    font-size: 8.6px; line-height: 11.8px; text-align: justify;
  }
  .letter-body p { margin-bottom: 11.8px; }
  .closing { position: absolute; left: 42px; top: 594px; font-size: 8.6px; }
  .signature {
    width: 80px; height: 46px; margin: 10px 0 10px 18px;
    background: linear-gradient(90deg, #f2f2f2, #e4e4e4);
    border-radius: 4px;
  }
  .signer { font-weight: 700; }
  .footer-line {
    position: absolute; left: 0; bottom: 44px;
    width: 100%; height: 3px; background: var(--rule-grey);
  }
  .footer-band {
    position: absolute; left: 0; bottom: 0;
    width: 100%; height: 40px; background: var(--purple);
  }
</style>
</head>
<body>
  <main class="letterhead">
    <div class="brand">Meridian Realty Group, LLC</div>

    <ul class="contact">
      <li>
        <svg viewBox="0 0 24 24" fill="none" stroke="var(--purple)" stroke-width="1.6"><path d="M12 21s-6-6.2-6-11a6 6 0 0 1 12 0c0 4.8-6 11-6 11z"/><circle cx="12" cy="10" r="2.3"/><path d="M7 21h10"/></svg>
        <span>123, Your Address Goes Here,<br>NY, USA- 123456</span>
      </li>
      <li>
        <svg viewBox="0 0 24 24" fill="none" stroke="var(--purple)" stroke-width="1.6"><circle cx="12" cy="12" r="10"/><path d="M8.5 7.5l2 2-1 1.5a7 7 0 0 0 3.5 3.5l1.5-1 2 2-1.5 1.5c-3 0-7.5-4.5-7.5-7.5z"/></svg>
        <span>+0123 456 789<br>+0123 456 789</span>
      </li>
      <li>
        <svg viewBox="0 0 24 24" fill="none" stroke="var(--purple)" stroke-width="1.6"><circle cx="12" cy="12" r="10"/><path d="M2 12h20M12 2c3 3 3 17 0 20M12 2c-3 3-3 17 0 20"/></svg>
        <span>info@yourmailid.com<br>www.yourwebsite.com</span>
      </li>
    </ul>

    <div class="header-rule"></div>

    <section class="letter-body">
      <p>Lorem Ipsum is simply</p>
      <p>Dummy text of the printing and typesetting industry. Lorem Ipsum has been the industry's standard dummy text ever since the 1500s, when an unknown printer took a galley of type and scrambled it to make a type specimen book. It has survived not only five centuries, but also the leap into electronic typesetting, remaining essentially unchanged. It was popularised in the 1960s with the release of Typeleaf sheets containing Lorem Ipsum passages, and more recently with desktop publishing software like Quillset Pagecraft including versions of Lorem Ipsum.</p>
      <p>Lorem Ipsum is simply dummy text of the printing and typesetting industry. Lorem Ipsum has been the industry's standard dummy text ever since the 1500s, when an unknown printer took a galley of type and scrambled it to make a type specimen book. It has survived not only five centuries, but also the leap into electronic typesetting, remaining essentially unchanged. It was popularised in the 1960s with the release of Typeleaf sheets containing Lorem Ipsum passages, and more recently with desktop publishing software like Quillset Pagecraft including versions of Lorem Ipsum.</p>
      <p>Lorem Ipsum is simply dummy text of the printing and typesetting industry. Lorem Ipsum has been the industry's standard dummy text ever since the 1500s, when an unknown printer took a galley of type and scrambled it to make a type specimen book. It has survived not only five centuries, but also the leap into electronic typesetting, remaining essentially unchanged. It was popularised in the 1960s with the release of Typeleaf sheets containing Lorem Ipsum passages, and more recently with desktop publishing software like Quillset Pagecraft including versions of Lorem Ipsum.</p>
      <p>Lorem Ipsum is simply dummy text of the printing and typesetting industry. Lorem Ipsum has been the industry's standard dummy text ever since the 1500s, when an unknown printer took a galley of type and scrambled it to make a type specimen book. It has survived not only five centuries, but also the leap into electronic typesetting, remaining essentially unchanged. It was popularised in the 1960s with the release of Typeleaf sheets containing Lorem Ipsum passages, and more recently with desktop publishing software like Quillset Pagecraft including versions of Lorem Ipsum.Lorem Ipsum is simply dummy text of the printing and typesetting industry. Lorem Ipsum has been the industry's standard dummy text ever since the 1500s, when an unknown printer took a galley of type and scrambled it to make a type specimen book.</p>
    </section>

    <div class="closing">
      <div>Lorem Ipsum Dummy Text</div>
      <div class="signature" role="img" aria-label="Handwritten signature"></div>
      <div class="signer">Lorem Ipsum Dummy Text</div>
    </div>

    <div class="footer-line"></div>
    <div class="footer-band"></div>
  </main>
</body>
</html>
```